New business card/stationary for a consulting company

I am looking for a clean and very professional looking business card for my consulting company as well as corresponding stationary. I am uploading our logo. I like simple and powerful for the feel. No graphics but I am open on everything else. Below is my contact information but would like the final to be in a version I can add my employees information into and print. Thank you.

Daniel Whitcombe
dan@ferncliffadvisory.com
2870 North 9th Avenue, Summit Floor, Elm Ridge, Illinois 60531
www.ferncliffadvisory.com

Industry/Entity Type

Consulting

Contact Information for Business Card

Daniel Whitcombe
dan@ferncliffadvisory.com
www.ferncliffadvisory.com

Font styles to use
Serif
Sans Serif

Requirements
Must have
• Our logo and the business card details.
Nice to have
• our website www.ferncliffadvisory.com

```html
<!DOCTYPE html>
<html lang="en">
<head>
<meta charset="utf-8">
<title>Ferncliff Advisory — Business Card</title>
<link rel="stylesheet" href="https://fonts.googleapis.com/css2?family=Questrial&family=Montserrat:wght@700&family=Roboto:wght@400&display=swap">
<style>
  :root {
    --page-bg: #e4e2de;
    --card-top: #f4f5f6;
    --card-bottom: #e7e9eb;
    --navy: #1c1b4d;
    --navy-deep: #15143d;
    --name-band: #b9b8b4;
    --contact-text: #d9d3e6;
    --shadow: rgba(20, 20, 40, 0.18);
  }
  html, body {
    margin: 0;
    padding: 0;
    width: 1200px;
    height: 969px;
    overflow: hidden;
    background: var(--page-bg);
  }
  .canvas {
    position: relative;
    width: 1200px;
    height: 969px;
  }
  .business-card {
    position: absolute;
    left: 100px;
    top: 200px;
    width: 1000px;
    height: 569px;
    background: linear-gradient(180deg, var(--card-top) 0%, var(--card-bottom) 100%);
    box-shadow: 0 18px 40px var(--shadow);
    overflow: hidden;
  }
  .brand-mark {
    position: absolute;
    left: 460px;
    top: 109px;
    width: 80px;
    height: 80px;
    background: var(--navy);
  }
  .brand-name {
    position: absolute;
    left: 0;
    top: 228px;
    width: 100%;
    margin: 0;
    text-align: center;
    font-family: "Questrial", sans-serif;
    font-weight: 400;
    font-size: 46px;
    letter-spacing: 2px;
    color: var(--navy);
    line-height: 1;
  }
  .name-band {
    position: absolute;
    left: 0;
    top: 359px;
    width: 100%;
    height: 72px;
    background: var(--name-band);
    display: flex;
    align-items: center;
    justify-content: center;
  }
  .person-name {
    margin: 0;
    font-family: "Montserrat", sans-serif;
    font-weight: 700;
    font-size: 31px;
    letter-spacing: 1.5px;
    text-transform: uppercase;
    color: var(--navy);
  }
  .contact-band {
    position: absolute;
    left: 0;
    top: 431px;
    width: 100%;
    height: 138px;
    background: linear-gradient(180deg, var(--navy) 0%, var(--navy-deep) 100%);
    border-top: 2px solid #d8d6e0;
    box-sizing: border-box;
    display: flex;
    flex-direction: column;
    align-items: center;
    justify-content: flex-start;
    padding-top: 26px;
  }
  .contact-line {
    margin: 0 0 8px;
    font-family: "Roboto", sans-serif;
    font-size: 23px;
    line-height: 1.2;
    color: var(--contact-text);
  }
</style>
</head>
<body>
<main class="canvas">
  <section class="business-card">
    <div class="brand-mark" aria-hidden="true"></div>
    <h1 class="brand-name">FERNCLIFF ADVISORY</h1>
    <div class="name-band">
      <p class="person-name">Daniel Whitcombe</p>
    </div>
    <div class="contact-band">
      <p class="contact-line">2870 North 9th Avenue, Summit Floor, Elm Ridge, Illinois 60531</p>
      <p class="contact-line">dan@ferncliffadvisory.com | www.ferncliffadvisory.com</p>
    </div>
  </section>
</main>
</body>
</html>
```